Request for Business Card Design

Hi. My name is Marlene, I am looking for a new business card design for my company, Quarrow Signal Instruments, LLC. I really like the design you did for Tarsel Venture and was hoping you could do something similar using our full logo and our mark. I am also open to any raised texture design using our mark. I have attached our full logo, which would need to be somewhere on the card, as well as the mark in both outline and full form, as well as our brand colors / guide. The card does not have to be white, as long as our logo and mark appear. I actually like darker colored business cards more, but am open to all options. If you are interested in working with me, please let me know. We would also take the business card design into letterhead design if you can do that.

```html
<!DOCTYPE html>
<html lang="en">
<head>
<meta charset="utf-8">
<title>Quarrow Signal Instruments – Business Card</title>
<link rel="stylesheet" href="https://fonts.googleapis.com/css2?family=Barlow+Semi+Condensed:wght@600&family=Poppins:wght@400;700&display=swap">
<style>
  :root {
    --stage: #2a2a2b;
    --card: #1b1c1e;
    --card-back: #161618;
    --accent: #1aa0c8;
    --ink: #ffffff;
    --rule: #6b6c70;
  }
  * { box-sizing: border-box; margin: 0; padding: 0; }
  html, body { width: 1200px; height: 1108px; overflow: hidden; }
  body {
    background: var(--stage);
    font-family: "Poppins", sans-serif;
    color: var(--ink);
    display: flex;
    align-items: center;
    justify-content: center;
    gap: 60px;
  }
  .card {
    width: 400px;
    height: 640px;
    border-radius: 22px;
    position: relative;
    overflow: hidden;
  }
  .card-front {
    background: var(--card);
    display: flex;
    flex-direction: column;
    align-items: center;
    padding-top: 90px;
  }
  .brand { display: flex; flex-direction: column; align-items: center; }
  .brand-dot {
    width: 64px; height: 64px; border-radius: 50%;
    background: var(--accent);
    margin-bottom: 22px;
  }
  .brand-name {
    font-weight: 700;
    font-size: 50px;
    letter-spacing: 6px;
    line-height: 1;
  }
  .brand-tagline {
    font-size: 13px;
    letter-spacing: 1.5px;
    margin-top: 8px;
    text-transform: uppercase;
  }
  .person { margin-top: 60px; text-align: center; }
  .person-name {
    font-family: "Barlow Semi Condensed", sans-serif;
    font-weight: 600;
    font-size: 32px;
    color: var(--accent);
    letter-spacing: 1px;
    line-height: 1;
  }
  .person-title {
    font-size: 14px;
    letter-spacing: 1px;
    margin-top: 4px;
    text-transform: uppercase;
  }
  .icon-row {
    display: flex; align-items: center; gap: 6px;
    margin-top: 18px; width: 290px;
  }
  .icon-row .rule { flex: 1; height: 1px; background: var(--rule); }
  .icon {
    width: 26px; height: 26px; border-radius: 4px;
    background: var(--accent);
    display: flex; align-items: center; justify-content: center;
  }
  .contact { text-align: center; margin-top: 10px; font-size: 16px; line-height: 1.45; }
  .divider { width: 290px; height: 1px; background: var(--rule); margin: 18px 0 16px; }
  .address { text-align: center; font-size: 15px; line-height: 1.45; }

  .card-back { background: var(--card-back); }
  .back-texture {
    position: absolute; inset: 0;
    background: linear-gradient(225deg, #5b5c60 0%, #2c2d30 40%, #141416 75%, #0d0d0e 100%);
    opacity: 0.85;
  }
  .back-name {
    position: absolute;
    right: 70px; bottom: 150px;
    font-weight: 700;
    font-size: 18px;
    letter-spacing: 2px;
    color: var(--accent);
  }
</style>
</head>
<body>
  <section class="card card-front">
    <div class="brand">
      <span class="brand-dot"></span>
      <span class="brand-name">QUARROW</span>
      <span class="brand-tagline">Signal Instruments</span>
    </div>

    <div class="person">
      <p class="person-name">MARLENE ADAIR</p>
      <p class="person-title">Managing Director</p>
    </div>

    <div class="icon-row">
      <span class="rule"></span>
      <span class="icon" aria-label="Phone">
        <svg width="16" height="16" viewBox="0 0 24 24"><path fill="#1b1c1e" d="M6.6 10.8a15 15 0 0 0 6.6 6.6l2.2-2.2c.3-.3.7-.4 1-.2 1.1.4 2.3.6 3.6.6.6 0 1 .4 1 1V20c0 .6-.4 1-1 1A17 17 0 0 1 3 4c0-.6.4-1 1-1h3.5c.6 0 1 .4 1 1 0 1.3.2 2.5.6 3.6.1.3 0 .7-.2 1z"/></svg>
      </span>
      <span class="icon" aria-label="Email">
        <svg width="16" height="16" viewBox="0 0 24 24"><rect x="3" y="6" width="18" height="12" fill="none" stroke="#1b1c1e" stroke-width="2"/><path d="M3 6l9 7 9-7" fill="none" stroke="#1b1c1e" stroke-width="2"/></svg>
      </span>
      <span class="icon" aria-label="Website">
        <svg width="16" height="16" viewBox="0 0 24 24"><circle cx="12" cy="12" r="9" fill="#1b1c1e"/></svg>
      </span>
      <span class="rule"></span>
    </div>

    <div class="contact">
      <p>044-555 010 203</p>
      <p>info@quarrowsignal.com</p>
      <p>www.quarrowsignal.com</p>
    </div>

    <span class="divider"></span>

    <div class="address">
      <p>88, Kestrel Row, Suite 4</p>
      <p>20418, Northland</p>
    </div>
  </section>

  <section class="card card-back">
    <div class="back-texture" role="img" aria-label="Raised gloss texture of repeated brand marks across the card back"></div>
    <span class="back-name">QUARROW</span>
  </section>
</body>
</html>
```